Luxury Toilet Rental Business. Tallowby Hire.

Tallowby Hire (the logo is in the uploaded files)
We RENT and SELL Luxury Trailer toilets.
- Show location, number, pricing, pictures.
- We have two stall trailers for rent AND 3 stall trailers
- We sell them too
- We want our phone number shown
- We are a local company
- Slogan: Brighten your gathering with Tallowby Hire. The Velvet Privy
- We want a pricing portion
- We want the sizes shown
- We want the different rates/ prices shown
- We do 1 day rentals
- We do 1 week rentals
- We want the service area. We serve Los Angeles County, Orange County, Riverside County, San Bernardino County, and Palm Desert.
- Our location is in Santa Ana California

Target Market(s)

Event planners, wedding planners, venue planners, concerts, events, gatherings.

Industry/Entity Type

Luxury Toilet Rentals

Number of Pages Required

1 page

Font styles to use
Serif
Sans Serif

Colors
EE7325
F08F49
F5BC92
FAE3D3
FDF4ED

Requirements
Must have
• Location, pricing, pictures, available areas. Our slogan.
Nice to have
• I like the idea of having tabs that show price, a tab that shows our contact information, pictures, event ideas, and where we service (the areas we'll go to)

```html
<!DOCTYPE html>
<html lang="en">
<head>
<meta charset="utf-8">
<title>Tallowby Hire — Landing Page Mobile View</title>
<link href="https://fonts.googleapis.com/css2?family=Roboto:wght@300;400;500;700&display=swap" rel="stylesheet">
<style>
  :root{
    --orange:#EE7325;
    --orange-mid:#F08F49;
    --orange-soft:#F5BC92;
    --peach:#FAE3D3;
    --cream:#FDF4ED;
    --ink:#1d1d1f;
    --grey-text:#5b5b5b;
    --slate:#5a5a5d;
    --charcoal:#3b3c40;
    --footer:#1e1e1e;
    --white:#ffffff;
  }
  *{box-sizing:border-box;margin:0;padding:0}
  html,body{width:780px;height:1200px;overflow:hidden;background:#fff}
  body{font-family:'Roboto',sans-serif;color:var(--ink)}
  .board{position:absolute;left:0;top:0;width:1480px;height:2277px;transform:scale(0.52703);transform-origin:0 0}
  .abs{position:absolute}

  .board-brand{left:115px;top:168px;display:flex;align-items:center;gap:22px}
  .board-brand .mark{width:58px;height:58px;background:var(--orange)}
  .board-brand .name{font-size:64px;font-weight:700;color:#4a4a4a;letter-spacing:1px}
  .board-title{left:115px;top:318px;font-size:40px;font-weight:500;color:var(--ink)}

  .screen{position:absolute;width:377px;overflow:hidden;background:var(--white);border-radius:34px;box-shadow:0 0 0 1px #e3e3e3}
  .screen-home{left:546px;top:450px;height:1752px}
  .screen-contact{left:1003px;top:48px;height:2154px}

  .site-header{left:0;top:0;width:377px;height:88px;background:var(--white)}
  .brand-small{left:24px;top:28px;display:flex;align-items:center;gap:7px}
  .brand-small .mark{width:14px;height:14px;background:var(--orange)}
  .brand-small .name{font-size:19px;font-weight:700;color:#4a4a4a}
  .menu-icon{left:325px;top:31px}

  .hero{left:0;top:88px;width:377px;height:600px;background:linear-gradient(180deg,#7a6a4c 0%,#5b5852 25%,#46474a 60%,#3a3b3d 100%)}
  .hero-title{left:20px;top:214px;width:337px;text-align:center;font-size:30px;font-weight:700;line-height:38px;color:var(--cream);text-shadow:0 0 3px var(--orange),0 0 1px var(--orange)}
  .hero-sub{left:22px;top:358px;width:333px;text-align:center;font-size:19px;line-height:23px;color:var(--white)}
  .btn{display:flex;align-items:center;justify-content:center;font-weight:500;letter-spacing:1.5px;text-transform:uppercase;color:var(--white)}
  .btn-rent{left:36px;top:460px;width:151px;height:55px;background:var(--orange);font-size:19px}
  .btn-buy{left:204px;top:460px;width:136px;height:55px;border:2px solid var(--white);font-size:19px;font-weight:400}

  .section-title{font-size:30px;font-weight:700;color:var(--ink)}
  .trailer-heading{left:0;top:790px;width:377px;text-align:center}

  .trailer-card{left:24px;top:858px;width:329px;height:674px;background:var(--white);box-shadow:0 2px 6px rgba(0,0,0,.22)}
  .trailer-photo{left:0;top:0;width:329px;height:280px;background:linear-gradient(180deg,#d9dadb 0%,#b9bbbd 35%,#8c8d8f 60%,#a7a8aa 100%)}
  .photo-arrow{top:225px;width:30px;height:30px;background:rgba(40,40,40,.55);display:flex;align-items:center;justify-content:center}
  .photo-arrow.prev{left:24px}
  .photo-arrow.next{left:274px}
  .trailer-name{left:24px;top:303px;font-size:20px;font-weight:400;color:var(--ink)}
  .trailer-size{left:24px;top:335px;font-size:15px;color:#333}
  .trailer-desc{left:24px;top:378px;width:282px;font-size:15px;line-height:19px;font-weight:300;color:var(--grey-text)}
  .period-select{left:24px;top:517px;width:99px;height:30px;border:1px solid #bdbdbd;font-size:13px;display:flex;align-items:center;justify-content:space-between;padding:0 10px}
  .price{left:132px;top:518px;font-size:20px;font-weight:700;color:var(--ink);white-space:nowrap}
  .price small{font-size:13px;font-weight:400}
  .price-info{left:289px;top:520px;width:10px;height:10px;border:1px solid #777;border-radius:50%}
  .btn-rent-now{left:24px;top:564px;width:154px;height:50px;background:var(--orange);font-size:16px}
  .buy-link{left:24px;top:631px;font-size:15px;color:var(--ink);text-decoration:underline}

  .pager{top:1588px;width:48px;height:48px;display:flex;align-items:center;justify-content:center}
  .pager.prev{left:132px;background:#c9c9c9}
  .pager.next{left:196px;background:var(--orange-soft)}

  .service-band{left:0;top:0;width:377px;height:646px;background:var(--slate)}
  .service-map{left:0;top:0;width:377px;height:282px;background:linear-gradient(160deg,#6a6a6d 0%,#5e5e61 60%,#5a5a5d 100%)}
  .light{color:var(--white)}
  .service-heading{left:24px;top:318px}
  .service-text{left:24px;top:387px;width:330px;font-size:19px;line-height:23px}
  .framed{border:2px solid var(--white);padding:4px}
  .framed .inner{background:var(--orange);height:100%;display:flex;align-items:center;justify-content:center;gap:10px;color:var(--white);font-size:16px;font-weight:500}
  .call-frame{left:24px;top:511px;width:256px;height:64px}
  .contact-link{left:24px;top:590px;font-size:19px;color:var(--white);text-decoration:underline}

  .contact-band{left:0;top:646px;width:377px;height:849px;background:linear-gradient(180deg,#34363a 0%,#3f4044 50%,#47484b 100%)}
  .contact-heading{left:24px;top:746px}
  .contact-text{left:24px;top:816px;width:320px;font-size:19px;line-height:23px}
  .contact-frame{left:24px;top:917px;width:155px;height:63px}
  .want-row{left:24px;top:1012px;width:330px;height:47px;display:flex;align-items:center;font-size:19px;color:var(--white);white-space:nowrap}
  .want-select{margin:0 9px;width:145px;height:47px;background:var(--white);color:var(--ink);display:flex;align-items:center;justify-content:space-between;padding:0 16px}
  .field{left:24px;width:329px;height:47px;background:var(--white);font-size:19px;color:#9a9a9a;padding:12px 12px}
  .field.name{top:1067px}
  .field.email{top:1122px}
  .field.event{top:1177px}
  .field.message{top:1232px;height:100px}
  .btn-submit{left:24px;top:1340px;width:329px;height:55px;background:var(--orange);font-size:19px;letter-spacing:2px}

  .site-footer{left:0;top:1495px;width:377px;height:659px;background:var(--footer);color:var(--white)}
  .footer-brand{left:32px;top:76px;display:flex;align-items:center;gap:8px}
  .footer-brand .mark{width:16px;height:16px;background:var(--orange)}
  .footer-brand .name{font-size:22px;font-weight:700;color:var(--orange)}
  .foot-h{left:24px;font-size:20px;font-weight:500}
  .foot-p{left:24px;font-size:15px;line-height:19px}
  .news-input{left:24px;top:509px;width:231px;height:42px;border:1px solid var(--white);font-size:15px;padding:11px 11px}
  .news-submit{left:24px;top:561px;width:112px;height:42px;background:var(--orange);font-size:15px;letter-spacing:1.5px}
</style>
</head>
<body>
<div class="board">

  <div class="abs board-brand"><span class="mark"></span><span class="name">Tallowby Hire</span></div>
  <h1 class="abs board-title">Landing Page Mobile View</h1>

  <section class="screen screen-home">
    <header class="abs site-header">
      <div class="abs brand-small"><span class="mark"></span><span class="name">Tallowby Hire</span></div>
      <svg class="abs menu-icon" width="24" height="18" viewBox="0 0 24 18"><g stroke="#EE7325" stroke-width="2.2"><line x1="0" y1="2" x2="24" y2="2"/><line x1="0" y1="9" x2="24" y2="9"/><line x1="0" y1="16" x2="24" y2="16"/></g></svg>
    </header>

    <div class="abs hero" role="img" aria-label="Photo of a luxury restroom trailer parked in front of a building"></div>
    <h2 class="abs hero-title">Brighten your gathering with Tallowby Hire. The Velvet Privy</h2>
    <p class="abs hero-sub">Impress your guests with our lavish restroom options, adding a touch of refinement to your event.</p>
    <a class="abs btn btn-rent">Rent</a>
    <a class="abs btn btn-buy">Buy</a>

    <h2 class="abs section-title trailer-heading">Our Trailer</h2>
    <article class="abs trailer-card">
      <div class="abs trailer-photo" role="img" aria-label="Photo of a grey two-stall restroom trailer on a paved yard"></div>
      <span class="abs photo-arrow prev"><svg width="12" height="18" viewBox="0 0 12 18"><polyline points="9,2 3,9 9,16" fill="none" stroke="#fff" stroke-width="2.4"/></svg></span>
      <span class="abs photo-arrow next"><svg width="12" height="18" viewBox="0 0 12 18"><polyline points="3,2 9,9 3,16" fill="none" stroke="#fff" stroke-width="2.4"/></svg></span>
      <h3 class="abs trailer-name">Trailer Name 1</h3>
      <p class="abs trailer-size">Size: 7’ x 11’</p>
      <p class="abs trailer-desc">Lorem ipsum dolor sit amet consectetur. Nulla ac velit pharetra id pharetra at turpis libero. Amet sit dolor nisl massa tortor nulla magna enim nibh. Duis aliquam ultrices nisi pharetra massa augue cursus.</p>
      <div class="abs period-select"><span>1 Week</span><svg width="10" height="6" viewBox="0 0 10 6"><polyline points="1,1 5,5 9,1" fill="none" stroke="#333" stroke-width="1.2"/></svg></div>
      <p class="abs price">$123 - $456 <small>/week</small></p>
      <span class="abs price-info"></span>
      <a class="abs btn btn-rent-now">Rent Now</a>
      <a class="abs buy-link">Want to buy this trailer?</a>
    </article>

    <span class="abs pager prev"><svg width="16" height="26" viewBox="0 0 16 26"><polyline points="13,2 3,13 13,24" fill="none" stroke="#fff" stroke-width="3"/></svg></span>
    <span class="abs pager next"><svg width="16" height="26" viewBox="0 0 16 26"><polyline points="3,2 13,13 3,24" fill="none" stroke="#fff" stroke-width="3"/></svg></span>
  </section>

  <section class="screen screen-contact">
    <div class="abs service-band"></div>
    <div class="abs service-map" role="img" aria-label="Map of Southern California counties with service location markers"></div>
    <h2 class="abs section-title light service-heading">Service Areas</h2>
    <p class="abs light service-text">Lorem ipsum dolor sit amet consectetur. Morbi molestie fames mollis vel tellus cursus. Enim turpis volutpat ut nunc mauris.</p>
    <div class="abs framed call-frame"><div class="inner">
      <svg width="16" height="16" viewBox="0 0 24 24"><path fill="#fff" d="M6.6 10.8a15.1 15.1 0 0 0 6.6 6.6l2.2-2.2c.3-.3.7-.4 1-.2 1.1.4 2.3.6 3.6.6.6 0 1 .4 1 1V20c0 .6-.4 1-1 1A17 17 0 0 1 3 4c0-.6.4-1 1-1h3.5c.6 0 1 .4 1 1 0 1.3.2 2.5.6 3.6.1.3 0 .7-.2 1z"/></svg>
      <span>Call Us: 7145550198</span></div></div>
    <a class="abs contact-link">Contact Us</a>

    <div class="abs contact-band" role="img" aria-label="Dimmed photo of restroom trailer doors"></div>
    <h2 class="abs section-title light contact-heading">Contact Us</h2>
    <p class="abs light contact-text">Do you have any questions, or want to discuss with us? Feel free to fill form below, or call us immediately</p>
    <div class="abs framed contact-frame"><div class="inner">Contact Us</div></div>
    <div class="abs want-row">I want to<span class="want-select">Rental<svg width="10" height="6" viewBox="0 0 10 6"><polyline points="1,1 5,5 9,1" fill="none" stroke="#333" stroke-width="1.2"/></svg></span>loo trailer.</div>
    <div class="abs field name">Name</div>
    <div class="abs field email">Email</div>
    <div class="abs field event">Event</div>
    <div class="abs field message">Message</div>
    <a class="abs btn btn-submit">Submit</a>

    <footer class="abs site-footer">
      <div class="abs footer-brand"><span class="mark"></span><span class="name">Tallowby Hire</span></div>
      <h4 class="abs foot-h" style="top:151px">Location</h4>
      <p class="abs foot-p" style="top:192px">5821 Larkspur Lane<br>Santa Ana, CA 92701</p>
      <h4 class="abs foot-h" style="top:260px">Phone</h4>
      <p class="abs foot-p" style="top:301px">7145550198</p>
      <h4 class="abs foot-h" style="top:350px">Trailers</h4>
      <p class="abs foot-p" style="top:391px">For Rent</p>
      <p class="abs foot-p" style="top:418px">For Sell</p>
      <h4 class="abs foot-h" style="top:467px">Newsletter</h4>
      <div class="abs news-input">youremail@mailbox.test</div>
      <a class="abs btn news-submit">Submit</a>
    </footer>
  </section>

</div>
</body>
</html>
```